Business Card Design

New business card design

Target Market(s)

Residential & Commercial Property Managers

Industry/Entity Type

Plumbing Services

Contact Information for Business Card

Name - Rowan Keddle, title - Director, Phone Number - 0431 286 517, email - rowan@tbk-plumbing.com.au, Company ABN - 73 215 904 386,

Font styles to use
Sans Serif

Colors
0054AA
0677BA
7BADD7
CADEEF
E8F1F8

```html
<!DOCTYPE html>
<html lang="en">
<head>
<meta charset="utf-8">
<title>TBK Plumbing Services – Business Card</title>
<link href="https://fonts.googleapis.com/css2?family=Montserrat:wght@700&family=Roboto:wght@300;400&display=swap" rel="stylesheet">
<style>
  :root {
    --backdrop: #2b2c2e;
    --card-dark: #1f242a;
    --card-light: #ffffff;
    --accent: #0ba7e8;
    --ink-light: #ffffff;
    --ink-dark: #1f242a;
  }
  * { margin: 0; padding: 0; box-sizing: border-box; }
  html, body {
    width: 1200px; height: 1015px; overflow: hidden;
    background: var(--backdrop);
  }
  .canvas {
    width: 1200px; height: 1015px;
    display: flex; flex-direction: column; align-items: center; justify-content: center;
    gap: 70px;
  }
  .card {
    position: relative;
    width: 620px; height: 376px;
    background: var(--card-dark);
    overflow: hidden;
    box-shadow: 0 10px 30px rgba(0,0,0,0.45);
  }
  .card-front {
    display: flex; align-items: center; justify-content: center;
  }
  .brand {
    display: flex; align-items: center; gap: 12px;
    font-family: "Roboto", sans-serif; font-weight: 300;
    color: var(--ink-light);
    white-space: nowrap;
  }
  .brand-dot {
    width: 18px; height: 18px; border-radius: 50%;
    background: var(--accent); flex: none;
  }
  .card-front .brand-name { font-size: 40px; letter-spacing: 3px; }
  .card-back .backdrop-shape { position: absolute; inset: 0; }
  .card-back .brand {
    position: absolute; left: 328px; top: 128px;
    color: var(--ink-dark);
  }
  .card-back .brand-name { font-size: 21px; letter-spacing: 1px; }
  .card-back .brand-dot { width: 11px; height: 11px; }
  .contact {
    position: absolute; left: 36px; top: 150px;
    font-family: "Roboto", sans-serif; color: var(--ink-light);
  }
  .person-name {
    font-family: "Montserrat", sans-serif; font-weight: 700;
    font-size: 20px; color: var(--accent); letter-spacing: 0.5px;
  }
  .person-title { font-size: 15px; margin-left: 10px; font-weight: 400; }
  .contact-list { list-style: none; margin-top: 26px; margin-left: 22px; }
  .contact-list li {
    display: flex; align-items: center; gap: 8px;
    font-size: 14px; font-weight: 300; line-height: 22px;
  }
  .contact-list svg { width: 15px; height: 15px; flex: none; }
  .company-abn {
    margin-top: 34px; margin-left: 22px;
    font-size: 14px; font-weight: 300;
  }
</style>
</head>
<body>
<main class="canvas">

  <section class="card card-front" aria-label="Business card front">
    <div class="brand">
      <span class="brand-dot"></span>
      <span class="brand-name">TBK Plumbing Services</span>
    </div>
  </section>

  <section class="card card-back" aria-label="Business card back">
    <svg class="backdrop-shape" viewBox="0 0 620 376" width="620" height="376" aria-hidden="true">
      <circle cx="492" cy="150" r="212" fill="var(--accent)"/>
      <circle cx="502" cy="144" r="202" fill="var(--card-light)"/>
    </svg>

    <div class="brand">
      <span class="brand-dot"></span>
      <span class="brand-name">TBK Plumbing Services</span>
    </div>

    <div class="contact">
      <h1 class="person-name">ROWAN KEDDLE</h1>
      <p class="person-title">Director</p>
      <ul class="contact-list">
        <li>
          <svg viewBox="0 0 24 24" aria-label="Phone"><path fill="var(--accent)" d="M6.6 10.8a15 15 0 0 0 6.6 6.6l2.2-2.2a1 1 0 0 1 1-.25 11.4 11.4 0 0 0 3.6.57 1 1 0 0 1 1 1V20a1 1 0 0 1-1 1A17 17 0 0 1 3 4a1 1 0 0 1 1-1h3.5a1 1 0 0 1 1 1c0 1.25.2 2.45.57 3.57a1 1 0 0 1-.25 1z"/></svg>
          <span>0431 286 517</span>
        </li>
        <li>
          <svg viewBox="0 0 24 24" aria-label="Email"><path fill="var(--accent)" d="M2 5h20v14H2z"/><path fill="none" stroke="var(--card-dark)" stroke-width="1.6" d="M2 5l10 8 10-8"/></svg>
          <span>rowan@tbk-plumbing.com.au</span>
        </li>
      </ul>
      <p class="company-abn">Company ABN - 73 215 904 386</p>
    </div>
  </section>

</main>
</body>
</html>
```